Buch-/E-Book-Cover für Referenzbuch der Industrie
Zielgruppe
Als Manufaktur einzigartiger Fachmedien präsentiert verlag-technova Schlüsseltechnologien und ihre Märkte. Faszination für Technik ist die Grundlage unserer Arbeit. Mehr als 30 Jahre verlegerische Erfahrung und das Verständnis für Technologiemärkte machen uns zu einem anerkannten Partner der Industrie.
Unsere Medienmarken knüpfen ein starkes und weit verzweigtes Netzwerk – Print und digital – , in dem sich Anbieter und Anwender von Technologien und Produkten in ihren Zielsetzungen wiederfinden.
Unsere Magazine, Events und Netzwerkveranstaltungen sowie kundenspezifische Kommunikations- & Strategiekampagnen setzen in ihren Zielmärkten Maßstäbe und genießen bei Lesern, Kunden und Partnern Vertrauen und Respekt.
Für das ausgeschriebene Projekt handelt es sich um unsere Referenzpublikation MACHINA.ahead LUMEVETA.
LUMEVETA {polynesisch: Freiraum}
Das Referenzbuch der Industrie. Für Vorwärtsdenker und Zukunftsmacher.
Wandel bestimmt unsere Zeit und verändert unsere Gesellschaft, unsere Unternehmen, uns alle.
Im Wandel liegt Freiraum zur Gestaltung. Gesellschaftlicher Wandel, Technologie-Wandel, Klimawandel, Wertewandel, Führungswandel oder Organisationswandel sind nur einige Beispiele. Wer dabei den Wandel in engen Bahnen denkt, verschenkt Potential. Veränderung braucht Freiraum für neue Ideen und Perspektiven sowie Persönlichkeiten, die diesen nutzen wollen.
Aber wer gestaltet die Zukunft der Industrie und ihrer Branchen? Und wie?
Wir geben Personen aus der Industrie den Freiraum, ihre Perspektiven auf und aus dem Wandel zu erzählen. Warum? Weil sie uns begeistert haben, in persönlichen Treffen und Gesprächen, durch streitbare Meinungen und ehrliche Geschichten. Weil sie die Zukunft verändern.
LUMEVETA ist eine Aufforderung: Zum Mitdenken, Weiterdenken, aber auch Nachdenken.
LUMEVETA – RAUM FÜR NEUES
Ein Referenzbuch, d..
Aufgabenstellung
1. Kurzzusammenfassung der Ausschreibung
Die 4. Ausgabe des jährlichen Referenzbuchs der Industrie, MACHINA.ahead LUMEVETA 2025, erscheint im Oktober 2024. Für das Cover sucht der verlag-technova Verlag neue Vorschläge, die die Themen Freiraum und Wandel in den Fokus stellen.
2. Gestalterische & Inhaltliche Anforderungen
• Format: 195x250 mm + Anschnitt
• Rücken: ca. 1,6 cm (Stand letzte Publikation 2023)
• Auflösung: Druckqualität, mind. 300 dpi
• Inhaltliche Elemente:
- LUMEVETA Schriftzug
- {polynesisch: Freiraum}
- Untersatz: Das Referenzbuch der Industrie. Für Vorwärtsdenker und Zukunftsmacher.
- part of MACHINA.ahead Logo-Balken am unteren Rand (siehe Beispiel AuD_Titelbeispiel_Logobalken)
WICHTIG: Der aktuelle Schriftzug LUMEVETA und die Farbe Orange (0/80/100/0) (siehe Beispiel LUMEVETA 2021) sollen als Wiedererkennung in die Gestaltungen eingebunden werden.

```html
<!DOCTYPE html>
<html lang="de">
<head>
<meta charset="utf-8">
<title>LUMEVETA 2025 – Cover</title>
<link rel="stylesheet" href="https://fonts.googleapis.com/css2?family=Anton&family=Cinzel:wght@400;700&family=Oswald:wght@300;400&family=Quicksand:wght@400&display=swap">
<style>
  :root {
    --stage: #e8e3d8;
    --paper: #f4f4f3;
    --orange: #d8642f;
    --ink: #151515;
    --grey: #555555;
    --art-dark: #2a2a2a;
    --art-light: #9a9a9a;
  }
  html, body {
    margin: 0;
    width: 861px;
    height: 1200px;
    overflow: hidden;
    background: var(--stage);
  }
  .cover {
    position: absolute;
    left: 40px;
    top: 100px;
    width: 780px;
    height: 1000px;
    background: var(--paper);
    overflow: hidden;
    box-shadow: 0 6px 24px rgba(0,0,0,0.12);
  }
  .cover-graphics {
    position: absolute;
    inset: 0;
  }
  .wordmark-row {
    position: absolute;
    margin: 0;
    font-family: "Anton", "Oswald", sans-serif;
    font-size: 205px;
    line-height: 1;
    letter-spacing: -2px;
    color: var(--orange);
    -webkit-text-stroke: 3px var(--ink);
  }
  .row-lu { left: 18px;  top: 100px; }
  .row-me { left: 70px;  top: 262px; }
  .row-ve { left: 150px; top: 440px; }
  .row-ta { left: 128px; top: 604px; }
  .letter-art {
    position: absolute;
    background: linear-gradient(160deg, var(--art-dark), var(--art-light));
    border-radius: 6px;
  }
  .art-upper { left: 128px; top: 150px; width: 60px; height: 120px; }
  .art-lower { left: 232px; top: 492px; width: 70px; height: 110px; }
  .subtitle-tag {
    position: absolute;
    left: 262px;
    top: 86px;
    font-family: "Quicksand", sans-serif;
    font-size: 12px;
    color: var(--grey);
    transform: rotate(-0deg);
  }
  .edition-year {
    position: absolute;
    right: 30px;
    top: 300px;
    margin: 0;
    font-family: "Cinzel", serif;
    font-weight: 700;
    font-size: 40px;
    color: var(--ink);
  }
  .tagline {
    position: absolute;
    right: 30px;
    top: 352px;
    margin: 0;
    text-align: right;
    font-family: "Cinzel", serif;
    font-size: 17px;
    line-height: 1.2;
    color: var(--ink);
  }
  .series-bar {
    position: absolute;
    right: 30px;
    top: 782px;
    display: flex;
    align-items: baseline;
    gap: 10px;
    color: var(--ink);
  }
  .series-bar .part-of {
    font-family: "Oswald", sans-serif;
    font-weight: 300;
    font-size: 18px;
  }
  .series-bar .series-name {
    font-family: "Oswald", sans-serif;
    font-weight: 400;
    font-size: 34px;
    letter-spacing: 0.5px;
  }
</style>
</head>
<body>
  <main class="cover">
    <svg class="cover-graphics" width="780" height="1000" viewBox="0 0 780 1000" aria-hidden="false">
      <line class="rule-top" x1="0" y1="78" x2="780" y2="78" stroke="var(--orange)" stroke-width="5"/>
      <line class="rule-middle" x1="0" y1="432" x2="780" y2="432" stroke="var(--orange)" stroke-width="4"/>
      <line class="rule-bottom" x1="300" y1="832" x2="780" y2="832" stroke="var(--orange)" stroke-width="5"/>
      <defs>
        <linearGradient id="triangleArt" x1="0" y1="0" x2="1" y2="1">
          <stop offset="0" stop-color="#f0f0f0"/>
          <stop offset="0.6" stop-color="#8a8a8a"/>
          <stop offset="1" stop-color="#222"/>
        </linearGradient>
      </defs>
      <polygon class="triangle-frame" points="262,110 560,110 412,400" fill="var(--paper)" stroke="var(--orange)" stroke-width="5"/>
      <polygon class="triangle-art" role="img" aria-label="Illustration: Turbine mit aufsteigenden Pfeilen" points="300,125 535,125 412,370" fill="url(#triangleArt)"/>
    </svg>

    <span class="subtitle-tag">{polynesisch: Freiraum}</span>

    <h1 class="wordmark" aria-label="LUMEVETA">
      <span class="wordmark-row row-lu">LU</span>
      <span class="wordmark-row row-me">ME</span>
      <span class="wordmark-row row-ve">VE</span>
      <span class="wordmark-row row-ta">TA</span>
    </h1>
    <div class="letter-art art-upper" role="img" aria-label="Illustration: Kopfsilhouette mit Zahnrädern"></div>
    <div class="letter-art art-lower" role="img" aria-label="Illustration: Kopfsilhouette mit Maschinenteilen"></div>

    <p class="edition-year">2025</p>
    <p class="tagline">LUMEVETA<br>Das Referenzbuch<br>der Industrie.<br>Für Vorwärtsdenker<br>und Zukunftsmacher.</p>

    <div class="series-bar">
      <span class="part-of">part of</span>
      <span class="series-name">MACHINA.AHEAD</span>
    </div>
  </main>
</body>
</html>
```